Cocktail-Making Assistant App re-design

Ok boys and girls, here's the deal:
I have an android app which is almost complete, but needs a design overhaul.

The app is a standard cocktail-making assistant: gives you a list of cocktails and the ability to see which cocktail you can make out of those ingredients (drinks, fruit, etc) you have at home.

I've attached some general app flow, as well as detailed requirements/explanation presentation. Most of those things are just FYI, so that you know what it's about.

3 screens are the most important (main screen, cocktail view screen, ingredient view screen), meaning I will pick the design mostly based on ideas for those 3 things, with the fourth being a rather simple list (given on attached flow, third tier)
Some other screens are derived from that, with some minor changes on it, but you shouldn't care about that.

There are lots of other, non-explained things which I said nothing about only because they are (from design point of view) completely the same and would only make it seem more complicated.

I don't want to influence the colour scheme, but the app will be released under RedFig developer name (having a light colured red fig as a logo) so I suppose some brownish design, for example, will not really fit nicely. If you, however, have a killer which you are confident will prove me wrong, I'm looking forward to seeing it!

It should be a serious, elegant look (as opposed to cartoonish, but we are not aiming for a business look at all!), not cluttered with details, no clubbing themes, glitter and so on.

Test apk file available on request (Android 2.3+).

Edit: payment is now guaranteed
Also please note that currently, the favorite, "heart" button has a motion effect:
on click it flies out of the screen to the left (white heart) and comes back to the screen as a red heart. Take that into consideration, if it means anything to you.

Target Market(s)

Whoever you imagine would enjoy drinking cocktails

Industry/Entity Type

Business

Requirements
Must have
• Everything is said in the provided documentation - images say more than I could possibly write here.
Nice to have
• As said, most of the icons are a nice-to-have. Only those which are critically linked to the rest of the design must be provided. More details in the docs.
Should not have
• No cartoon look, No zillion colours

```html
<!DOCTYPE html>
<html lang="en">
<head>
<meta charset="utf-8">
<title>Cocktail-Making Assistant App</title>
<link href="https://fonts.googleapis.com/css2?family=Michroma&family=Open+Sans:ital,wght@0,400;0,600;1,400&display=swap" rel="stylesheet">
<style>
  :root {
    --stage: #d6d3d4;
    --ink: #111111;
    --screen: #ffffff;
    --accent-red: #b5121b;
    --rule: #dddddd;
    --muted: #8a8a8a;
    --tile-green: #a6cf6a;
    --tile-orange: #f7b35c;
    --tile-red: #f25c5c;
    --tile-rose: #c9ada6;
    --tile-yellow: #fbe37c;
    --tile-lavender: #b2a6e8;
    --star-green: #7cc36a;
    --star-orange: #f5a34a;
    --star-purple: #a38ce0;
    --star-pink: #e98fae;
    --star-grey: #555555;
    --title-font: "Michroma", sans-serif;
    --body-font: "Open Sans", sans-serif;
  }
  * { box-sizing: border-box; margin: 0; padding: 0; }
  html, body { width: 1200px; height: 900px; overflow: hidden; }
  body {
    background: radial-gradient(circle at 62% 40%, #f3f2f2 0%, var(--stage) 60%, #b9b5b6 100%);
    font-family: var(--body-font);
    color: var(--ink);
    position: relative;
  }
  .icon-defs { position: absolute; width: 0; height: 0; }
  .showcase-title {
    position: absolute; left: 125px; top: 96px;
    font-family: var(--title-font); font-size: 30px; letter-spacing: 3px;
    text-transform: uppercase; font-weight: 400;
  }
  .screen-row {
    position: absolute; left: 55px; top: 190px;
    display: flex; gap: 30px;
  }
  .screen {
    width: 250px; height: 480px; background: var(--screen);
    box-shadow: 0 8px 24px rgba(0,0,0,0.25);
    display: flex; flex-direction: column; overflow: hidden;
  }
  .screen-header {
    height: 46px; display: flex; align-items: center; gap: 8px;
    padding: 0 10px; border-bottom: 3px solid var(--accent-red);
    font-family: var(--title-font); font-size: 10px; letter-spacing: 1px;
    text-transform: uppercase; flex-shrink: 0;
  }
  .screen-header .header-title { flex: 1; line-height: 1.35; }
  .icon { width: 22px; height: 22px; fill: var(--ink); flex-shrink: 0; }

  /* Cocktail search */
  .search-field {
    margin: 8px 10px; height: 26px; border-radius: 13px; background: #ececec;
    display: flex; align-items: center; padding: 0 10px;
    font-family: var(--title-font); font-size: 8px; color: var(--muted); flex-shrink: 0;
  }
  .search-field span { flex: 1; text-align: center; }
  .search-field .icon { width: 12px; height: 12px; fill: var(--muted); }
  .cocktail-grid {
    flex: 1; min-height: 0; display: grid; grid-template-columns: 1fr 1fr; grid-template-rows: repeat(4, 1fr);
    border-top: 1px solid var(--rule);
  }
  .cocktail-cell {
    border-right: 1px solid var(--rule); border-bottom: 1px solid var(--rule);
    display: grid; grid-template-columns: 1fr 28px; grid-template-rows: 42px auto auto;
    align-content: start; padding: 5px 6px; gap: 3px 2px; min-height: 0; overflow: hidden;
  }
  .cocktail-cell:nth-child(2n) { border-right: none; }
  .cocktail-photo { border-radius: 4px; height: 42px; }
  .stock {
    font-family: var(--title-font); font-size: 5.5px; color: var(--muted);
    text-align: center; line-height: 1.3;
  }
  .stock .icon { width: 12px; height: 12px; display: block; margin: 0 auto 2px; }
  .cocktail-name {
    grid-column: 1 / -1; font-family: var(--title-font); font-size: 6.5px; font-weight: 400;
    text-transform: uppercase; line-height: 1.25;
  }
  .stars { grid-column: 1 / -1; font-size: 9px; letter-spacing: 1px; line-height: 1; }
  .s-green { color: var(--star-green); } .s-orange { color: var(--star-orange); }
  .s-purple { color: var(--star-purple); } .s-pink { color: var(--star-pink); }
  .s-grey { color: var(--star-grey); }

  /* Cocktail view */
  .cocktail-summary {
    display: flex; align-items: center; padding: 10px 12px; gap: 8px;
    border-bottom: 1px solid var(--rule); height: 72px; flex-shrink: 0;
  }
  .cocktail-summary .summary-text { flex: 1; }
  .summary-status { font-family: var(--title-font); font-size: 7px; text-transform: uppercase; margin-top: 4px; }
  .favourite-button { width: 36px; height: 36px; }
  .ingredient-list { list-style: none; flex: 1; display: flex; flex-direction: column; }
  .ingredient-row {
    flex: 1; display: flex; align-items: center; justify-content: space-between;
    padding: 0 12px; font-family: var(--title-font); font-size: 9px; text-transform: uppercase;
  }
  .ingredient-row .icon { width: 28px; height: 28px; }
  .row-green { background: var(--tile-green); }
  .row-orange { background: var(--tile-orange); }
  .row-red { background: var(--tile-red); }
  .row-rose { background: var(--tile-rose); }
  .find-link {
    height: 44px; display: flex; align-items: center; justify-content: center;
    font-family: var(--title-font); font-size: 7px; color: var(--muted); text-transform: uppercase;
    flex-shrink: 0;
  }

  /* Ingredient view */
  .ingredient-summary {
    display: flex; align-items: center; justify-content: space-between;
    padding: 8px 12px; border-bottom: 1px solid var(--rule); height: 58px; flex-shrink: 0;
  }
  .ingredient-summary h2 { font-family: var(--title-font); font-size: 8px; font-weight: 400; text-transform: uppercase; }
  .bottle-photo { width: 22px; height: 44px; border-radius: 3px; }
  .ingredient-story {
    flex: 1; padding: 10px 14px; font-size: 7.5px; line-height: 1.55; font-style: italic;
    background: #f5f5f5;
  }
  .ingredient-story p + p { margin-top: 8px; }
  .ingredient-footer {
    height: 48px; display: flex; align-items: center; justify-content: center; gap: 10px;
    border-top: 1px solid var(--rule); font-family: var(--title-font); font-size: 7px;
    text-transform: uppercase; flex-shrink: 0;
  }

  /* Main screen */
  .main-bar {
    height: 40px; display: flex; align-items: center; gap: 10px; padding: 0 12px;
    border-bottom: 1px solid var(--rule); font-family: var(--title-font); font-size: 9px;
    flex-shrink: 0;
  }
  .main-bar .bar-count { flex: 1; }
  .main-bar .icon { width: 18px; height: 18px; }
  .tile-grid { flex: 1; display: grid; grid-template-columns: 1fr 1fr; grid-template-rows: repeat(3, 1fr); }
  .tile { display: flex; align-items: center; justify-content: center; }
  .tile .icon { width: 64px; height: 64px; }
  .tile-green { background: var(--tile-green); }
  .tile-orange { background: var(--tile-orange); }
  .tile-red { background: var(--tile-red); }
  .tile-rose { background: var(--tile-rose); }
  .tile-yellow { background: var(--tile-yellow); }
  .tile-lavender { background: var(--tile-lavender); }
</style>
</head>
<body>

<svg class="icon-defs" aria-hidden="true">
  <defs>
    <symbol id="icon-home" viewBox="0 0 24 24"><path d="M12 3 2 12h3v9h5v-6h4v6h5v-9h3z"/></symbol>
    <symbol id="icon-search" viewBox="0 0 24 24"><circle cx="10" cy="10" r="6" fill="none" stroke="currentColor" stroke-width="3"/><path d="M14 14l7 7" stroke="currentColor" stroke-width="3"/></symbol>
    <symbol id="icon-camera" viewBox="0 0 24 24"><path d="M8 5l2-2h4l2 2h5a1 1 0 0 1 1 1v13a1 1 0 0 1-1 1H3a1 1 0 0 1-1-1V6a1 1 0 0 1 1-1z"/><circle cx="12" cy="12" r="5" fill="#fff"/><circle cx="12" cy="12" r="3"/></symbol>
    <symbol id="icon-shaker" viewBox="0 0 24 24"><path d="M10 2h4v3h-4zM8 6h8l-1 3H9zM8 10h8l-1 12H9z"/></symbol>
    <symbol id="icon-cart" viewBox="0 0 24 24"><path d="M2 4h3l3 10h11l2-7H7" fill="none" stroke="#111" stroke-width="2"/><circle cx="9" cy="18" r="2"/><circle cx="17" cy="18" r="2"/><rect x="11" y="2" width="3" height="9" rx="1"/></symbol>
    <symbol id="icon-heart-plus" viewBox="0 0 24 24"><path d="M11 20 3 12a5 5 0 0 1 8-6 5 5 0 0 1 8 6z"/><circle cx="18" cy="17" r="5.5" fill="#fff" stroke="#111" stroke-width="1.5"/><path d="M18 14v6M15 17h6" stroke="#111" stroke-width="1.8"/></symbol>
    <symbol id="icon-bar" viewBox="0 0 24 24"><circle cx="17" cy="4" r="2.2"/><path d="M15 7h4v8h-4zM13 15h6v2h-6zM14 17h2v5h-2zM6 9h5v6H6zM11 10h2v3h-2zM3 15h11v1.5H3zM5 16.5h1.5V22H5z"/></symbol>
    <symbol id="icon-badge" viewBox="0 0 24 24"><path d="M12 1l2.5 2.5 3.5-.5.5 3.5L21 9l-1.5 3 1.5 3-2.5 2.5-.5 3.5-3.5-.5L12 23l-2.5-2.5-3.5.5-.5-3.5L3 15l1.5-3L3 9l2.5-2.5L6 3l3.5.5z"/></symbol>
    <symbol id="icon-menu" viewBox="0 0 24 24"><path d="M3 5h18v3H3zM3 11h18v3H3zM3 17h18v3H3z"/></symbol>
    <symbol id="icon-gear" viewBox="0 0 24 24"><circle cx="12" cy="12" r="7" fill="none" stroke="#111" stroke-width="4" stroke-dasharray="3 2.5"/><circle cx="12" cy="12" r="4"/><circle cx="12" cy="12" r="1.8" fill="#fff"/></symbol>
  </defs>
</svg>

<h1 class="showcase-title">Cocktail-Making Assistant App</h1>

<main class="screen-row">

  <section class="screen screen-search" aria-label="Cocktail search screen">
    <header class="screen-header">
      <svg class="icon"><use href="#icon-home"/></svg>
      <span class="header-title">Cocktail Search</span>
    </header>
    <div class="search-field"><span>Search all</span><svg class="icon" style="color:var(--muted)"><use href="#icon-search"/></svg></div>
    <div class="cocktail-grid">
      <article class="cocktail-cell">
        <div class="cocktail-photo" role="img" aria-label="Photo of an amber drink in a tulip glass" style="background:linear-gradient(#f4f4f4,#e8d9a0)"></div>
        <div class="stock"><svg class="icon"><use href="#icon-shaker"/></svg>Have<br>0 of 5</div>
        <h3 class="cocktail-name">'57 Cruiser</h3>
        <div class="stars"><span class="s-green">★</span><span class="s-orange">★</span><span class="s-purple">★</span><span class="s-pink">★</span></div>
      </article>
      <article class="cocktail-cell">
        <div class="cocktail-photo" role="img" aria-label="Photo of a pink drink in a tall glass" style="background:linear-gradient(#fbe1e4,#ee6f7c)"></div>
        <div class="stock"><svg class="icon"><use href="#icon-shaker"/></svg>Have<br>0 of 5</div>
        <h3 class="cocktail-name">'57 Cruiser #2</h3>
        <div class="stars"><span class="s-green">★</span><span class="s-orange">★</span><span class="s-purple">★</span><span class="s-pink">★</span></div>
      </article>
      <article class="cocktail-cell">
        <div class="cocktail-photo" role="img" aria-label="Photo of a red drink in a goblet" style="background:linear-gradient(#f6e4e6,#c3132c)"></div>
        <div class="stock"><svg class="icon"><use href="#icon-shaker"/></svg>Have<br>0 of 5</div>
        <h3 class="cocktail-name">'57 Cruiser with a white license plate</h3>
        <div class="stars"><span class="s-green">★</span><span class="s-orange">★</span><span class="s-grey">★</span></div>
      </article>
      <article class="cocktail-cell">
        <div class="cocktail-photo" role="img" aria-label="Photo of a green drink with mint" style="background:linear-gradient(#eef5dc,#9cc24a)"></div>
        <div class="stock"><svg class="icon"><use href="#icon-shaker"/></svg>Have<br>0 of 4</div>
        <h3 class="cocktail-name">1-900-Fuk-Meup</h3>
        <div class="stars"><span class="s-grey">★★★★</span></div>
      </article>
      <article class="cocktail-cell">
        <div class="cocktail-photo" role="img" aria-label="Photo of a blue drink with lime" style="background:linear-gradient(#e4f5fb,#2fa8e0)"></div>
        <div class="stock"><svg class="icon"><use href="#icon-shaker"/></svg>Have<br>0 of 4</div>
        <h3 class="cocktail-name">110 in the Shade</h3>
        <div class="stars"><span class="s-green">★</span><span class="s-orange">★</span><span class="s-grey">★★</span></div>
      </article>
      <article class="cocktail-cell">
        <div class="cocktail-photo" role="img" aria-label="Photo of orange and cola drinks with fruit" style="background:linear-gradient(#fbe7c8,#e27a1c)"></div>
        <div class="stock"><svg class="icon"><use href="#icon-shaker"/></svg>Have<br>0 of 4</div>
        <h3 class="cocktail-name">151 Florida Bushwacker</h3>
        <div class="stars"><span class="s-green">★</span><span class="s-orange">★</span><span class="s-purple">★</span><span class="s-pink">★</span></div>
      </article>
      <article class="cocktail-cell">
        <div class="cocktail-photo" role="img" aria-label="Photo of a cocktail" style="background:linear-gradient(#f1f1f1,#d9c7b0)"></div>
        <div class="stock"><svg class="icon"><use href="#icon-shaker"/></svg>Have<br>0 of 3</div>
        <h3 class="cocktail-name">24 Karat Nightmare</h3>
        <div class="stars"><span class="s-green">★</span><span class="s-grey">★★★</span></div>
      </article>
      <article class="cocktail-cell">
        <div class="cocktail-photo" role="img" aria-label="Photo of a cocktail" style="background:linear-gradient(#f1f1f1,#e6a7b6)"></div>
        <div class="stock"><svg class="icon"><use href="#icon-shaker"/></svg>Have<br>0 of 6</div>
        <h3 class="cocktail-name">252 Shooter</h3>
        <div class="stars"><span class="s-green">★</span><span class="s-orange">★</span><span class="s-grey">★★</span></div>
      </article>
    </div>
  </section>

  <section class="screen screen-cocktail" aria-label="Cocktail view screen">
    <header class="screen-header">
      <span class="header-title">151 Florida<br>Bushwacker</span>
      <svg class="icon"><use href="#icon-camera"/></svg>
    </header>
    <div class="cocktail-summary">
      <div class="summary-text">
        <div class="stars"><span class="s-green">★</span><span class="s-orange">★</span><span class="s-purple">★</span><span class="s-pink">★</span><span class="s-grey">★</span></div>
        <div class="summary-status">Cocktail unavailable</div>
      </div>
      <svg class="icon favourite-button"><use href="#icon-heart-plus"/></svg>
    </div>
    <ul class="ingredient-list">
      <li class="ingredient-row row-green"><span>Coral Bay Rum</span><svg class="icon"><use href="#icon-cart"/></svg></li>
      <li class="ingredient-row row-orange"><span>Light Rum</span><svg class="icon"><use href="#icon-cart"/></svg></li>
      <li class="ingredient-row row-red"><span>151 Proof Rum</span><svg class="icon"><use href="#icon-cart"/></svg></li>
      <li class="ingredient-row row-rose"><span>Creme de Cacao</span><svg class="icon"><use href="#icon-cart"/></svg></li>
    </ul>
    <div class="find-link">Find the cocktail</div>
  </section>

  <section class="screen screen-ingredient" aria-label="Ingredient view screen">
    <header class="screen-header">
      <span class="header-title">Bellamy's<br>Irish Cream</span>
      <svg class="icon"><use href="#icon-camera"/></svg>
    </header>
    <div class="ingredient-summary">
      <h2>Irish Cream</h2>
      <div class="bottle-photo" role="img" aria-label="Photo of a dark liqueur bottle" style="background:linear-gradient(#4a3a2a,#1a120c)"></div>
    </div>
    <div class="ingredient-story">
      <p>Born in Ireland. Weaving together Irish whiskey and fresh cream to create a perfect blend of flavors, it pairs with refreshing beverages both hot and cold, bringing out the golden flavors of this classic.</p>
      <p>The cream and pure Irish whiskey form an emulsion with the help of a refined vegetable oil. This process keeps the blend from separating during storage.</p>
      <p>Only natural ingredients are required as the base; the cream used in the drink comes from local dairy farms.</p>
    </div>
    <div class="ingredient-footer">
      <svg class="icon"><use href="#icon-bar"/></svg>
      <span>Ingredients</span>
    </div>
  </section>

  <section class="screen screen-main" aria-label="Main screen">
    <div class="main-bar">
      <span class="bar-count">Ingredients : 100</span>
      <svg class="icon"><use href="#icon-menu"/></svg>
      <svg class="icon"><use href="#icon-gear"/></svg>
    </div>
    <div class="tile-grid">
      <div class="tile tile-green"></div>
      <div class="tile tile-orange"><svg class="icon"><use href="#icon-bar"/></svg></div>
      <div class="tile tile-red"></div>
      <div class="tile tile-rose"><svg class="icon"><use href="#icon-heart-plus"/></svg></div>
      <div class="tile tile-yellow"></div>
      <div class="tile tile-lavender"><svg class="icon"><use href="#icon-badge"/></svg></div>
    </div>
  </section>

</main>
</body>
</html>
```